Bramblewood Card Company Business Cards

We are a trading card store with Glimmorax, sports and other TCG cards, we need a business card design that encompasses a clean cut, modern style with a retro flare. website is bramblewoodcardco.com for reference. Can utilize a comic book era feel or a more modern outdoor feel to utilize the "Pacific Northwest" elements of tress, mountains, etc.

Industry/Entity Type

Trading cards and collectibles

Contact Information for Business Card

business name, email address, phone number, name, owner job title

Font styles to use
Sans Serif

```html
<!DOCTYPE html>
<html lang="en">
<head>
<meta charset="utf-8">
<title>Bramblewood Card Company – Business Cards</title>
<link href="https://fonts.googleapis.com/css2?family=Montserrat:wght@400;600;700&display=swap" rel="stylesheet">
<style>
  :root {
    --backdrop: #d3d6d7;
    --paper: #fbfbfa;
    --slate: #5c5d5f;
    --teal: #1fa1c4;
    --ink: #3c3d3f;
    --muted: #6a6b6d;
  }
  * { margin: 0; padding: 0; box-sizing: border-box; }
  html, body { width: 1200px; height: 829px; overflow: hidden; }
  body {
    background: var(--backdrop);
    font-family: "Montserrat", Arial, sans-serif;
    position: relative;
  }
  .card {
    position: absolute;
    top: 272px;
    width: 500px;
    height: 286px;
    border-bottom: 4px solid var(--teal);
    box-shadow: 0 14px 30px rgba(0,0,0,0.14);
  }
  .card-front { left: 60px; background: var(--paper); }
  .card-back { left: 640px; background: var(--slate); }

  .identity {
    position: absolute;
    right: 272px;
    top: 112px;
    text-align: right;
  }
  .identity .person {
    color: var(--teal);
    font-weight: 700;
    font-size: 24px;
    letter-spacing: 1px;
    text-transform: uppercase;
  }
  .identity .role {
    color: var(--muted);
    font-size: 15px;
    margin-top: 2px;
  }
  .divider {
    position: absolute;
    left: 246px;
    top: 100px;
    width: 1px;
    height: 96px;
    background: #c9cacb;
  }
  .contact {
    position: absolute;
    left: 262px;
    top: 96px;
    color: var(--ink);
    font-size: 13px;
    line-height: 20px;
    list-style: none;
  }
  .contact li { display: flex; align-items: center; gap: 7px; }
  .contact li.plain { padding-left: 0; }
  .contact svg { width: 10px; height: 10px; fill: var(--teal); flex: none; }

  .brand {
    position: absolute;
    inset: 0;
    display: flex;
    align-items: center;
    justify-content: center;
    gap: 12px;
  }
  .brand .dot {
    width: 14px; height: 14px; border-radius: 50%;
    background: var(--teal);
  }
  .brand .name {
    color: #f2f2f2;
    font-weight: 700;
    font-size: 20px;
    letter-spacing: 2px;
    text-transform: uppercase;
  }
</style>
</head>
<body>
  <section class="card card-front" aria-label="Business card front">
    <div class="identity">
      <p class="person">Dorian Vale</p>
      <p class="role">CEO/Founder</p>
    </div>
    <div class="divider"></div>
    <ul class="contact">
      <li class="plain">P.O. Box 3170 Lane</li>
      <li class="plain">Fernhollow WA 9817</li>
      <li>
        <svg viewBox="0 0 10 10" aria-hidden="true"><path d="M2 0.5 L3.8 2.6 L2.8 3.8 Q4 6.2 6.2 7.2 L7.4 6.2 L9.5 8 L8.2 9.6 Q3.5 9 0.4 1.8 Z"/></svg>
        (555) 318 2046
      </li>
      <li>
        <svg viewBox="0 0 10 10" aria-hidden="true"><path d="M0 2 H10 V8.5 H0 Z M0 2 L5 6 L10 2" stroke="#fbfbfa" stroke-width="0.8"/></svg>
        info@bramblewoodcardco.com
      </li>
      <li>
        <svg viewBox="0 0 10 10" aria-hidden="true"><circle cx="5" cy="5" r="4.8"/><path d="M0.5 5 H9.5 M5 0.3 V9.7 M5 0.3 Q1.8 5 5 9.7 M5 0.3 Q8.2 5 5 9.7" stroke="#fbfbfa" stroke-width="0.6" fill="none"/></svg>
        www.bramblewoodcardco.com
      </li>
    </ul>
  </section>

  <section class="card card-back" aria-label="Business card back">
    <div class="brand">
      <span class="dot"></span>
      <span class="name">Bramblewood Card Company</span>
    </div>
  </section>
</body>
</html>
```